Restaurant Menu New Design

Hello Designers,

Blue Fern is a casual family oriented dine-in restaurant, we serve American Italian dishes like Pizza, Pasta, and Sandwiches.

We are excited about adding some new delicious dishes and recipes to our menu. And we are looking for a talented and creative designer to design it.

The menu is a 12 page black leather book, page size is:
6.5" X 11.69" (16.51 cm X 29.69 cm)

Below is the scope of work and requirements:

1) Design a completely all new, creative, and beautiful menu, including cover page, blue fern oven intro. page, interior pages, and kids menu page.

2) Design a take out edition of the menu. It will be exactly the same as the dine-in menu, but with the addition of a back cover page with info such as contacts, social media, location map, etc…

3) Files are required in Adobe Illustrator format. Layers should be organized, all text should be editable, and all the food pictures easy to change.

4) This is a two language menu, so you are required to make space in the design for a second language. The easiest way to do that is have every item listed in English twice, then I will edit the second text with Illustrator.

5) In your initial design submission, the minimum you are required to submit are these 4 pages:
– Cover page
– Typical interior menu page
– Kids menu page
– Take-out menu back cover page

If your initial design is selected, then you are required to submit all remaining pages to complete the project.

In the link below, you will find:
1) Logo
2) New menu text in Excel
3) Food images (will take some time to upload)
4) The old dine-in and take out menu designs

https://www.filevaultra.com/sh/kq7tmwzabe3pxd/BBBrTnpLk41QaWmZpQ8V2X7Jd?dl=0

Thank you for stopping by and reading this brief. I hope you like this project and enjoy designing our new menu. Please let me know if you have any questions.

Cheers!

Project Deadline Extended
Reason: We have decided to extend the deadline due to the low number of submissions which was much lower than the expected submissions we were give by Brief Harbor.

```html
<!DOCTYPE html>
<html lang="en">
<head>
<meta charset="utf-8">
<title>Blue Fern — Starters</title>
<link rel="stylesheet" href="https://fonts.googleapis.com/css2?family=Lato:wght@400;700&family=Noto+Naskh+Arabic:wght@400;700&display=swap">
<style>
:root{
  --board:#323234;
  --chalk:#f4f4f4;
  --line:#d9d9d9;
  --muted:#a9a9ab;
  --photo-fries:#c98a32;
  --photo-fries-2:#e6b54a;
  --photo-dip:#d9c48c;
  --photo-dip-2:#3a2a22;
}
*{margin:0;padding:0;box-sizing:border-box}
html,body{width:1200px;height:2171px;overflow:hidden;background:var(--board)}
.menu-page{position:relative;width:1200px;height:2171px;background:var(--board);color:var(--chalk);font-family:"Lato",Arial,sans-serif}
.rule{position:absolute;background:var(--line)}
.section-title{position:absolute;top:62px;font-size:38px;font-weight:400;letter-spacing:1px;color:var(--chalk)}
.ornament{position:absolute;border:2px solid rgba(255,255,255,.55);border-radius:12px;background:rgba(255,255,255,.04)}
.photo{position:absolute}
.photo--fries{left:104px;top:258px;width:432px;height:286px;background:linear-gradient(135deg,var(--photo-fries-2),var(--photo-fries) 60%,#a0471f)}
.photo--dip{left:106px;top:854px;width:428px;height:514px;background:linear-gradient(180deg,#6b3a2a 0%,var(--photo-dip-2) 30%,var(--photo-dip) 55%,var(--photo-dip-2) 90%)}
.item{position:absolute;width:560px;text-align:center}
.item--right{left:600px}
.item--left{left:38px}
.item-name{font-size:26px;font-weight:700;line-height:32px;letter-spacing:.2px}
.item-name-ar{font-family:"Noto Naskh Arabic",serif;font-size:25px;font-weight:400;line-height:32px;direction:rtl}
.item-desc{margin-top:20px;font-size:17px;line-height:25px;color:var(--muted)}
.item-desc-ar{margin-top:14px;font-family:"Noto Naskh Arabic",serif;font-size:16px;line-height:24px;color:var(--muted);direction:rtl}
.price-line .item-name{font-size:27px}
.divider-pin{position:absolute;left:486px;width:228px;height:26px;border:2px solid var(--line);border-radius:13px}
</style>
</head>
<body>
<main class="menu-page">

  <!-- header -->
  <h1 class="section-title" style="left:253px">STARTERS</h1>
  <h1 class="section-title" style="left:793px">STARTERS</h1>
  <div class="rule" style="left:0;top:125px;width:320px;height:2px"></div>
  <div class="rule" style="left:668px;top:122px;width:532px;height:2px"></div>
  <div class="ornament" role="img" aria-label="Serving cloche line icon" style="left:535px;top:68px;width:130px;height:88px;border-radius:60px 60px 6px 6px"></div>
  <div class="ornament" role="img" aria-label="Tomato, onion and mushroom line icons" style="left:238px;top:146px;width:182px;height:54px"></div>
  <div class="ornament" role="img" aria-label="Pea pod, rosemary and mushroom line icons" style="left:767px;top:150px;width:240px;height:58px"></div>

  <!-- section one frames -->
  <div class="rule" style="left:68px;top:221px;width:338px;height:2px"></div>
  <div class="rule" style="left:87px;top:239px;width:319px;height:2px"></div>
  <div class="rule" style="left:68px;top:221px;width:2px;height:344px"></div>
  <div class="rule" style="left:554px;top:260px;width:2px;height:310px"></div>
  <div class="rule" style="left:232px;top:568px;width:324px;height:2px"></div>
  <div class="photo photo--fries" role="img" aria-label="Photo of chili cheese fries topped with beef chili and melted cheddar"></div>

  <div class="rule" style="left:648px;top:221px;width:482px;height:2px"></div>
  <div class="rule" style="left:1128px;top:321px;width:2px;height:236px"></div>
  <div class="rule" style="left:702px;top:557px;width:428px;height:2px"></div>

  <div class="ornament" role="img" aria-label="Spatula line icon" style="left:567px;top:258px;width:40px;height:110px"></div>
  <div class="ornament" role="img" aria-label="Onion line icon" style="left:578px;top:420px;width:40px;height:86px"></div>
  <div class="ornament" role="img" aria-label="Chili pepper line icons" style="left:572px;top:548px;width:100px;height:128px"></div>

  <div class="item item--right price-line" style="top:253px">
    <h2 class="item-name">ONION RINGS &nbsp;15 |</h2>
    <p class="item-name-ar">حلقات البصل &nbsp;15</p>
  </div>
  <div class="item item--right price-line" style="top:353px">
    <h2 class="item-name">CHEESE FRIES &nbsp;15 |</h2>
    <p class="item-name-ar">تشيز فرايز &nbsp;15</p>
  </div>
  <div class="item item--right price-line" style="top:452px">
    <h2 class="item-name">FRENCH FRIES &nbsp;10 |</h2>
    <p class="item-name-ar">بطاطس مقلية &nbsp;10</p>
  </div>

  <div class="item item--left" style="top:577px">
    <h2 class="item-name">CHILI CHEESE FRIES |</h2>
    <p class="item-name-ar">تشيلي تشيز فرايز</p>
    <p class="item-desc">French fries, topped with beef chili and melted<br>cheddar cheese &nbsp;19</p>
    <p class="item-desc-ar">بطاطس مقلية مغطاة بخلطة اللحم المفروم وجبنة<br>التشيدر الساخنة &nbsp;19</p>
  </div>
  <div class="item item--right" style="top:576px">
    <h2 class="item-name">STARTER SAMPLER |</h2>
    <p class="item-name-ar">تشكيلة مقبلات</p>
    <p class="item-desc">Includes Mozza Sticks, Chicken Tenders,<br>Onion Rings, and Chili Cheese Fries &nbsp;38</p>
    <p class="item-desc-ar">مكونة من الموزا ستيكس، أصابع الدجاج، حلقات<br>البصل، و تشيلي تشيز فرايز &nbsp;38</p>
  </div>

  <!-- divider -->
  <div class="rule" style="left:0;top:803px;width:1200px;height:2px"></div>
  <div class="divider-pin" role="img" aria-label="Rolling pin divider" style="top:791px;background:var(--board)"></div>

  <!-- section two -->
  <svg style="position:absolute;left:55px;top:845px" width="40" height="190" viewBox="0 0 40 190" aria-hidden="true">
    <path d="M30 2 C0 30 0 60 20 95 C40 130 30 160 14 188" fill="none" stroke="#d9d9d9" stroke-width="2"/>
  </svg>
  <div class="rule" style="left:68px;top:1042px;width:2px;height:345px"></div>
  <div class="rule" style="left:68px;top:1386px;width:446px;height:2px"></div>
  <div class="rule" style="left:1128px;top:873px;width:2px;height:326px"></div>
  <div class="photo photo--dip" role="img" aria-label="Photo of baked cheese and garlic dip in a skillet with bread sticks"></div>

  <div class="ornament" role="img" aria-label="Eggplant line icon" style="left:580px;top:888px;width:72px;height:62px"></div>
  <div class="ornament" role="img" aria-label="Mushroom line icon" style="left:578px;top:1043px;width:80px;height:110px"></div>
  <div class="ornament" role="img" aria-label="Beet line icon" style="left:566px;top:1295px;width:82px;height:86px"></div>
  <div class="ornament" role="img" aria-label="Cheese wedge line icon" style="left:590px;top:1555px;width:86px;height:96px"></div>
  <div class="ornament" role="img" aria-label="Carrot line icon" style="left:533px;top:1640px;width:70px;height:70px"></div>
  <div class="ornament" role="img" aria-label="Leaf line icon" style="left:578px;top:1775px;width:88px;height:82px"></div>

  <div class="rule" style="left:0;top:1689px;width:288px;height:2px"></div>
  <div class="rule" style="left:760px;top:1588px;width:440px;height:2px"></div>

  <div class="item item--right" style="top:848px">
    <h2 class="item-name">GARLIC BREAD STICKS |</h2>
    <p class="item-name-ar">قطع الخبز بالثوم</p>
    <p class="item-desc">Garlic bread sticks served with marinara sauce<br>8<br>with mozzarella cheese 13</p>
    <p class="item-desc-ar">قطع الخبز بالثوم مقدمة مع صوص المارينارا &nbsp;8<br>مع جبنة الموزاريلا &nbsp;13</p>
  </div>
  <div class="item item--right" style="top:1116px">
    <h2 class="item-name">BUFFALO TENDERS |</h2>
    <p class="item-name-ar">بفلو تندرز</p>
    <p class="item-desc">Chicken tenders covered in spicy buffalo<br>sauce, served with ranch dressing &nbsp;24</p>
    <p class="item-desc-ar">قطع من صدور الدجاج مقلية ومغطاة بصوص<br>البفلو الحار ومقدمة مع صوص الرانش &nbsp;24</p>
  </div>
  <div class="item item--right" style="top:1369px">
    <h2 class="item-name">CHICKEN TENDERS |</h2>
    <p class="item-name-ar">أصابع الدجاج</p>
    <p class="item-desc">Lightly breaded chicken breast strips, fried &amp;<br>served with honey mustard &amp; BBQ sauce &nbsp;19</p>
    <p class="item-desc-ar">قطع من صدور الدجاج مقلية ومقدمة مع صوص الخردل<br>بالعسل و الباربيكيو &nbsp;19</p>
  </div>
  <div class="item item--right" style="top:1611px">
    <h2 class="item-name">FETA &amp; OLIVES DIP |</h2>
    <p class="item-name-ar">الزيتون و الفيتا</p>
    <p class="item-desc">Marinated olives baked with feta cheese and<br>olive oil &nbsp;23</p>
    <p class="item-desc-ar">خليط الزيتون مع البهارات مخبوز مع شرائح جبنة<br>الفيتا و زيت الزيتون و يقدم مع الخبز &nbsp;23</p>
  </div>
  <div class="item item--right" style="top:1848px">
    <h2 class="item-name">MOZZA STICKS |</h2>
    <p class="item-name-ar">موزا ستيكس</p>
    <p class="item-desc">Crispy fried mozzarella cheese, served with<br>marinara<br>&amp; BBQ sauce &nbsp;15</p>
    <p class="item-desc-ar" style="margin-top:4px">جبنة موزاريلا مقلية ومقدمة مع صوص<br>المارينارا و الباربيكيو &nbsp;15</p>
  </div>

  <div class="item item--left" style="top:1411px">
    <h2 class="item-name">CHEESE &amp; GARLIC DIP |</h2>
    <p class="item-name-ar">الجبنة و الثوم</p>
    <p class="item-desc">Oven baked creamy garlic and cheese dip<br>served with<br>bread sticks &nbsp;25</p>
    <p class="item-desc-ar">خليط الجبنة و الثوم و الأعشاب مخبوز في الفرن<br>يقدم ساخن مع الخبز &nbsp;25</p>
  </div>
  <div class="item item--left" style="top:1735px">
    <h2 class="item-name">HOT CAPRESE | <span style="font-family:'Noto Naskh Arabic',serif;font-weight:400">هوت كابريسي</span></h2>
    <p class="item-desc" style="margin-top:26px">Tomato chunks marinated with olive oil, garlic,<br>and fresh basil. Oven baked with mozzarella<br>cheese and served with bread sticks &nbsp;19</p>
    <p class="item-desc-ar">قطع الطماطم المتبلة مع الريحان و الثوم و زيت<br>الزيتون، مخبوزة في الفرن مع جبنة الموزاريلا و<br>تقدم مع الخبز الساخن &nbsp;19</p>
  </div>

  <!-- bottom divider -->
  <div class="rule" style="left:0;top:2084px;width:1200px;height:2px"></div>
  <div class="divider-pin" role="img" aria-label="Rolling pin divider" style="top:2072px;background:var(--board)"></div>

</main>
</body>
</html>
```